Stationary Set Rebrand for Brennick

We are a Canadian Distribution and Service Company that was established in 1969. Over the past 5 decades we have expanded our business and have warehouses across Canada. We specialize in adhesive tapes, adhesives, films, safety, warehouse, shipping, janitorial and packaging supplies.

We have updated our logo design and would like a new corporate branding identity that includes a new fresh Stationary Set (Business Cards, Letterhead, Letterhead MS Word, Envelope, Presentation Folders, Email Signatures, Notepad Covers, etc.)

Target Market(s)

Industrial Business Sector

Font styles to use
Sans Serif

Colors
0054AA
0677BA
7BADD7
CADEEF
E8F1F8
0094D4
00A9DD
6FCCEA
C7EBF8
E9F6FB
00AB8E
00BBA5
67D7C9
C6EFE9
E9F9F6
EB3D1F
EC4F4E
F09395
F8D3D4
FCEDEE

Requirements
Should not have
• Colors not too light, darker colours preferred

```html
<!DOCTYPE html>
<html lang="en">
<head>
<meta charset="utf-8">
<title>Brennick Stationery Set</title>
<link href="https://fonts.googleapis.com/css2?family=Roboto:wght@300;400;500;900&family=Michroma&display=swap" rel="stylesheet">
<style>
:root{
  --backdrop:#3b3b3d;
  --ink:#231f20;
  --red:#d71920;
  --paper:#f7f3f4;
  --white:#ffffff;
  --muted:#5a5657;
  --rule:#c9c5c6;
}
*{box-sizing:border-box;margin:0;padding:0}
html,body{width:1200px;height:933px;overflow:hidden}
body{background:var(--backdrop);font-family:"Roboto",Arial,sans-serif;color:var(--ink);position:relative}
.piece{position:absolute;overflow:hidden}
.piece svg.shape{position:absolute;left:0;top:0}
.brand{position:absolute;display:flex;flex-direction:column;line-height:1;font-size:var(--s,17px)}
.brand-name{font-weight:900;font-size:1em;letter-spacing:-.02em}
.brand-tag{font-weight:500;font-size:.26em;margin-top:.12em;letter-spacing:.01em}
.brand.on-dark{color:var(--white)}
.brand.centered{align-items:center;transform:translateX(-50%)}
.brand.right{align-items:flex-end}
.small{font-size:5px;line-height:1.3}
.contact{position:absolute;font-size:5px;line-height:6.3px;color:var(--white)}
.contact li{list-style:none;display:flex;align-items:center;gap:3px}
.contact.right li{justify-content:flex-end}
.dot{width:3px;height:3px;background:var(--red);border-radius:50%;display:inline-block}

/* business card front */
.card-front{left:38px;top:102px;width:219px;height:124px;background:var(--white);border-radius:5px}
.card-front .divider{position:absolute;left:113px;top:32px;width:1px;height:62px;background:var(--rule)}
.card-front .holder{position:absolute;left:121px;top:33px;color:var(--muted);font-size:5px;line-height:6.4px}
.holder-name{font-family:"Michroma","Roboto",sans-serif;color:var(--red);font-size:7.5px;line-height:9px}
.holder-role{font-size:4.6px;margin-bottom:5px}
.card-front .web{position:absolute;right:18px;bottom:2px;color:var(--white);font-size:5px}
.card-front .holder li{list-style:none;display:flex;align-items:center;gap:3px}

/* business card back */
.card-back{left:34px;top:275px;width:223px;height:127px;background:var(--ink);border-radius:5px}

/* letterhead */
.letterhead{left:280px;top:44px;width:306px;height:431px;background:var(--paper)}
.letter{position:absolute;left:31px;top:104px;width:246px;color:var(--muted)}
.letter-greeting{font-size:8.5px;margin-bottom:14px}
.letter p{font-size:4.7px;line-height:7.3px;text-align:justify;margin-bottom:7px;font-weight:300;color:#4a4647}
.letter-close{font-size:4.8px;margin-top:10px}
.signature{width:40px;height:14px;margin:5px 0 6px;background:linear-gradient(90deg,transparent,#cfcacb 30%,#cfcacb 70%,transparent)}
.signer{font-size:6.5px}
.signer-role{font-size:4.8px}
.letterhead .address{position:absolute;right:29px;top:362px;font-size:4.8px;line-height:6.3px;text-align:right;color:var(--ink)}

/* envelopes */
.env-dl{left:632px;top:80px;width:312px;height:85px;background:var(--paper)}
.env-back{left:632px;top:198px;width:343px;height:157px;background:var(--paper)}
.env-front{left:612px;top:300px;width:345px;height:157px;background:var(--paper);box-shadow:0 2px 6px rgba(0,0,0,.35)}
.address-line{position:absolute;color:var(--white);font-size:4.8px}

/* notepads */
.pad{position:absolute;width:128px;height:188px}
.pad-rings{position:absolute;left:1019px;width:138px;height:10px;background:repeating-linear-gradient(90deg,#bdbdbd 0 1.5px,transparent 1.5px 5.5px)}
.pad-dark{left:1023px;top:77px;background:var(--ink);width:129px}
.pad-light{left:1025px;top:297px;background:var(--paper)}
.pad-lines{position:absolute;left:13px;right:11px;top:55px;height:108px;background:repeating-linear-gradient(180deg,transparent 0 9.2px,#b7b2b3 9.2px 9.7px)}
.pad-web{position:absolute;left:0;right:0;text-align:center;font-size:5px}

/* folders */
.folder-cover{left:47px;top:560px;width:510px;height:321px}
.cover-back{position:absolute;left:0;top:0;width:254px;height:321px;background:var(--ink)}
.cover-front{position:absolute;left:254px;top:0;width:256px;height:321px;background:var(--white);overflow:hidden}
.cover-back .address{position:absolute;left:0;right:0;top:250px;text-align:center;color:var(--white);font-size:5px;line-height:6.5px}
.cover-back .rule{position:absolute;left:112px;top:269px;width:30px;height:1px;background:var(--white)}
.cover-back .contact{left:0;right:0;top:276px;display:flex;flex-direction:column;align-items:center}
.folder-open{left:610px;top:562px;width:510px;height:322px}
.inner-half{position:absolute;top:0;height:192px;width:255px}
.inner-left{left:0;background:linear-gradient(90deg,#ffffff,#f1f1f1 70%,#dadada)}
.inner-right{left:255px;background:linear-gradient(90deg,#d6d6d6,#f3f3f3 25%,#ffffff)}
</style>
</head>
<body>

<!-- business card front -->
<section class="piece card-front" aria-label="Business card front">
  <div class="brand" style="--s:17px;left:24px;top:50px"><span class="brand-name">Brennick</span><span class="brand-tag">Tape and Packaging Specialists</span></div>
  <div class="divider"></div>
  <div class="holder">
    <div class="holder-name">DANIEL MOREAU</div>
    <div class="holder-role">President</div>
    <div>412 Alder Crescent</div>
    <div style="margin-bottom:4px">Thornbury, Canada 58216</div>
    <ul>
      <li><span class="dot"></span>705-218-4460</li>
      <li><span class="dot"></span>705-391-2287</li>
      <li><span class="dot"></span>info@brennick.com</li>
    </ul>
  </div>
  <svg class="shape" width="219" height="124" viewBox="0 0 219 124">
    <path d="M0 115 H140 Q146 115 148 112 L150 109 H219 V124 H0 Z" fill="var(--red)"/>
    <path d="M0 109 H142 L140 113 H0 Z" fill="var(--ink)"/>
  </svg>
  <div class="web">www.brennick.com</div>
</section>

<!-- business card back -->
<section class="piece card-back" aria-label="Business card back">
  <div class="brand on-dark centered" style="--s:27px;left:111px;top:44px"><span class="brand-name">Brennick</span><span class="brand-tag">Tape and Packaging Specialists</span></div>
</section>

<!-- letterhead -->
<section class="piece letterhead" aria-label="Letterhead">
  <svg class="shape" width="306" height="431" viewBox="0 0 306 431">
    <path d="M0 0 H306 V6 H112 Q108 6 106 10 L104 14 H0 Z" fill="var(--red)"/>
    <path d="M0 409 H168 Q178 409 184 400 L190 391 Q196 382 206 382 H306 V431 H0 Z" fill="var(--ink)"/>
  </svg>
  <div class="brand right" style="--s:17px;right:29px;top:29px"><span class="brand-name">Brennick</span><span class="brand-tag">Tape and Packaging Specialists</span></div>
  <div class="letter">
    <div class="letter-greeting">Dear Mr. Moreau,</div>
    <p>Lorem ipsum dolor sit amet, consectetur adipiscing elit. Donec orci purus, luctus vitae dignissim eu, iaculis sed purus. Vivamus faucibus, ipsum nec aliquet viverra, leo mauris condimentum ligula, sit amet sagittis enim ligula quis arcu. Nam egestas tortor id nisi porttitor mattis. In tortor ante, ultricies in suscipit a, tempus non massa. Vivamus et auctor mi. Fusce vel massa nulla. Phasellus nec eros mauris, et scelerisque orci.</p>
    <p>Donec malesuada orci vitae nulla accumsan porta a id massa. Quisque accumsan iaculis magna sit amet fringilla. Maecenas consequat, magna eget tincidunt semper, odio nibh rutrum mi, id feugiat ante nisi eu risus. Vestibulum nunc orci, rhoncus a placerat in, ultricies in mi. Cras mattis varius eros, vel fringilla nisi suscipit eget. Quisque scelerisque sagittis nulla at porttitor.</p>
    <p>Sed id augue vitae urna euismod commodo aliquet a quam. Pellentesque arcu velit, cursus et malesuada ut, consequat et diam. Nullam erat sem, rhoncus id ullamcorper vitae, rhoncus et arcu. In ultricies ultricies nulla, ut rutrum nisi iaculis at. Donec eu magna a metus ornare faucibus. Fusce aliquet faucibus ultricies. Morbi semper, est id tincidunt gravida, sem arcu adipiscing lacus, ac bibendum nulla leo eu purus. Quisque nec diam sed risus consectetur a accumsan quis quis nibh. Vestibulum id purus lorem.</p>
    <p>It is a long established fact that a reader will be distracted by the readable content of a page when looking at its layout. The point of using Lorem Ipsum is that it has a more-or-less normal distribution of letters, as opposed to using 'Content here, content here', making it look like readable English. Many desktop publishing packages</p>
    <div class="letter-close">Sincerely,</div>
    <div class="signature" role="img" aria-label="Handwritten signature"></div>
    <div class="signer">Daniel Moreau</div>
    <div class="signer-role">CEO/ Founder</div>
  </div>
  <div class="address">412 Alder Crescent<br>Thornbury, Canada 58216</div>
  <ul class="contact right" style="right:29px;top:394px">
    <li>705-218-4460<span class="dot"></span></li>
    <li>705-391-2287<span class="dot"></span></li>
    <li>info@brennick.com<span class="dot"></span></li>
    <li>www.brennick.com<span class="dot"></span></li>
  </ul>
</section>

<!-- DL envelope -->
<section class="piece env-dl" aria-label="Envelope">
  <svg class="shape" width="312" height="85" viewBox="0 0 312 85">
    <path d="M0 0 H312 V13 H218 Q215 13 214 10 L212 5 H0 Z" fill="var(--red)"/>
    <path d="M0 40 H95 Q102 40 107 47 L113 56 Q119 65 128 65 H312 V85 H0 Z" fill="var(--ink)"/>
  </svg>
  <div class="brand right" style="--s:17px;right:18px;top:30px"><span class="brand-name">Brennick</span><span class="brand-tag">Tape and Packaging Specialists</span></div>
  <ul class="contact" style="left:13px;top:53px">
    <li><span class="dot"></span>705-218-4460</li>
    <li><span class="dot"></span>705-391-2287</li>
    <li><span class="dot"></span>info@brennick.com</li>
    <li><span class="dot"></span>www.brennick.com</li>
  </ul>
  <div class="address-line" style="right:18px;top:72px">412 Alder Crescent, Thornbury, Canada 58216</div>
</section>

<!-- envelope back -->
<section class="piece env-back" aria-label="Envelope back">
  <svg class="shape" width="343" height="157" viewBox="0 0 343 157">
    <path d="M0 0 H343 L333 44 Q330 57 316 57 H27 Q13 57 10 44 Z" fill="var(--ink)"/>
  </svg>
  <div class="brand on-dark centered" style="--s:21px;left:171px;top:16px"><span class="brand-name">Brennick</span><span class="brand-tag">Tape and Packaging Specialists</span></div>
</section>

<!-- envelope front -->
<section class="piece env-front" aria-label="Envelope front">
  <svg class="shape" width="345" height="157" viewBox="0 0 345 157">
    <path d="M0 0 H345 V14 H240 Q237 14 236 11 L234 6 H0 Z" fill="var(--red)"/>
    <path d="M0 108 H105 Q112 108 117 115 L123 124 Q129 135 140 135 H345 V157 H0 Z" fill="var(--ink)"/>
  </svg>
  <div class="brand" style="--s:17px;left:18px;top:18px"><span class="brand-name">Brennick</span><span class="brand-tag">Tape and Packaging Specialists</span></div>
  <ul class="contact" style="left:18px;top:125px">
    <li><span class="dot"></span>705-218-4460</li>
    <li><span class="dot"></span>705-391-2287</li>
    <li><span class="dot"></span>info@brennick.com</li>
    <li><span class="dot"></span>www.brennick.com</li>
  </ul>
  <div class="address-line" style="right:21px;top:144px">412 Alder Crescent, Thornbury, Canada 58216</div>
</section>

<!-- notepads -->
<div class="pad-rings" style="top:72px"></div>
<section class="piece pad pad-dark" aria-label="Notepad cover">
  <div class="brand on-dark centered" style="--s:15px;left:64px;top:83px"><span class="brand-name">Brennick</span><span class="brand-tag">Tape and Packaging Specialists</span></div>
  <div class="pad-web" style="top:170px;color:var(--white)">www.brennick.com</div>
</section>
<div class="pad-rings" style="top:292px"></div>
<section class="piece pad pad-light" aria-label="Notepad page">
  <div class="brand centered" style="--s:11px;left:66px;top:19px"><span class="brand-name">Brennick</span><span class="brand-tag">Tape and Packaging Specialists</span></div>
  <div class="pad-lines"></div>
  <div class="pad-web" style="top:172px">www.brennick.com</div>
</section>

<!-- presentation folder, closed -->
<section class="piece folder-cover" aria-label="Presentation folder cover">
  <div class="cover-back">
    <div class="brand on-dark centered" style="--s:33px;left:127px;top:138px"><span class="brand-name">Brennick</span><span class="brand-tag">Tape and Packaging Specialists</span></div>
    <div class="address">412 Alder Crescent<br>Thornbury, Canada 58216</div>
    <div class="rule"></div>
    <ul class="contact">
      <li>705-218-4460 &nbsp; 705-391-2287</li>
      <li>info@brennick.com &nbsp; www.brennick.com</li>
    </ul>
  </div>
  <div class="cover-front">
    <svg class="shape" width="256" height="321" viewBox="0 0 256 321">
      <path d="M0 0 H256 V5 H93 Q90 5 89 8 L88 11 H0 Z" fill="var(--red)"/>
      <path d="M0 302 H150 Q158 302 163 295 L167 289 Q172 281 182 281 H256 V321 H0 Z" fill="var(--ink)"/>
    </svg>
    <div class="brand centered" style="--s:36px;left:128px;top:136px"><span class="brand-name">Brennick</span><span class="brand-tag">Tape and Packaging Specialists</span></div>
    <div class="pad-web" style="top:302px;left:auto;right:27px;color:var(--white)">www.brennick.com</div>
  </div>
</section>

<!-- presentation folder, open -->
<section class="piece folder-open" aria-label="Presentation folder inside">
  <div class="inner-half inner-left"></div>
  <div class="inner-half inner-right"></div>
  <svg class="shape" width="510" height="322" viewBox="0 0 510 322">
    <rect x="0" y="192" width="510" height="130" fill="#e4e4e4"/>
    <path d="M0 192 H225 Q236 192 237 204 L254 318 V322 H0 Z" fill="var(--ink)"/>
    <path d="M510 192 H285 Q274 192 273 204 L256 318 V322 H510 Z" fill="var(--ink)"/>
  </svg>
  <div class="brand on-dark centered" style="--s:29px;left:127px;top:238px"><span class="brand-name">Brennick</span><span class="brand-tag">Tape and Packaging Specialists</span></div>
  <div class="brand on-dark centered" style="--s:29px;left:391px;top:238px"><span class="brand-name">Brennick</span><span class="brand-tag">Tape and Packaging Specialists</span></div>
</section>

</body>
</html>
```